Business Card Design

Online clothing womens clothing store, I sell my clothing online and at the markets.

i would like the attached picture on the front of the card and the contact information on the back.

Industry/Entity Type

Business

Contact Information for Business Card

Marlow Thread
Karen Whitfield
(Instagram symbol) _marlow_thread_
(Facebook symbol) www.fakebookexample.com/marlowthreadau/

W : www.marlowthread.example.au
E : info@marlowthread.example.au
P : 0498716204

```html
<!DOCTYPE html>
<html lang="en">
<head>
<meta charset="utf-8">
<title>Marlow Thread — Business Card</title>
<link rel="stylesheet" href="https://fonts.googleapis.com/css2?family=Open+Sans:wght@400;600;700&display=swap">
<style>
  :root {
    --backdrop: #e6e4e1;
    --card-dark: #1c1d1f;
    --card-mid: #3a3c3f;
    --band-light: #c9cccf;
    --band-pale: #e4e6e8;
    --mist-pale: #eef1f2;
    --mist-blue: #b9c6c9;
    --mist-slate: #5d6670;
    --text-light: #f2f2f2;
    --text-soft: #d8d9db;
    --divider: rgba(255,255,255,0.28);
    --wordmark-faint: rgba(255,255,255,0.72);
  }
  * { box-sizing: border-box; margin: 0; padding: 0; }
  html, body {
    width: 1200px; height: 844px; overflow: hidden;
    background: var(--backdrop);
    font-family: "Open Sans", Arial, sans-serif;
  }
  .sheet {
    width: 1200px; height: 844px;
    display: flex; align-items: center; justify-content: center; gap: 40px;
  }
  .card {
    position: relative; width: 540px; height: 300px; overflow: hidden;
    box-shadow: 0 6px 18px rgba(0,0,0,0.18);
  }

  /* Back: contact side */
  .card--back {
    background: linear-gradient(160deg, var(--card-mid) 0%, var(--card-dark) 55%, #141516 100%);
  }
  .card--back .photo-fade {
    position: absolute; right: 0; top: 60px; width: 300px; height: 240px;
    background: radial-gradient(ellipse at 70% 70%, rgba(140,150,158,0.45) 0%, rgba(90,98,106,0.25) 45%, rgba(0,0,0,0) 75%);
  }
  .card--back .footer-band {
    position: absolute; left: 0; right: 0; bottom: 0; height: 70px;
    background: linear-gradient(180deg, var(--band-light), var(--band-pale));
    opacity: 0.9;
  }
  .holder-name {
    position: absolute; left: 32px; top: 150px;
    color: var(--text-light); font-weight: 600; font-size: 15px; letter-spacing: 0.3px;
  }
  .divider {
    position: absolute; left: 250px; top: 62px; width: 1px; height: 140px;
    background: var(--divider);
  }
  .contact-list {
    position: absolute; left: 262px; top: 64px; list-style: none;
    color: var(--text-soft); font-size: 11.5px; line-height: 17px;
  }
  .contact-list li { display: flex; align-items: center; gap: 8px; }
  .contact-list li.gap-before { margin-top: 12px; }
  .contact-list svg { width: 10px; height: 10px; flex: none; }
  .social-mark {
    width: 9px; height: 9px; flex: none; background: var(--text-soft); border-radius: 2px;
  }
  .wordmark {
    position: absolute; font-family: "Open Sans", Arial, sans-serif; font-weight: 700;
    text-transform: uppercase; letter-spacing: 4px; white-space: nowrap;
  }
  .card--back .wordmark {
    right: 26px; bottom: 78px; font-size: 42px; color: var(--wordmark-faint);
  }

  /* Front: photo side */
  .card--front .photo {
    position: absolute; inset: 0;
    background:
      radial-gradient(ellipse at 78% 40%, var(--mist-slate) 0%, rgba(93,102,112,0.6) 28%, rgba(185,198,201,0) 60%),
      linear-gradient(170deg, var(--mist-pale) 0%, var(--mist-blue) 55%, #9aa6ac 100%);
  }
  .card--front .wordmark {
    right: 24px; bottom: 22px; font-size: 44px; color: #ffffff;
  }
</style>
</head>
<body>
<main class="sheet">
  <section class="card card--back" aria-label="Card back with contact details">
    <div class="photo-fade" role="img" aria-label="Faded brand photograph behind the contact details"></div>
    <div class="footer-band"></div>
    <p class="holder-name">KAREN WHITFIELD</p>
    <div class="divider"></div>
    <ul class="contact-list">
      <li>
        <svg viewBox="0 0 10 10" aria-hidden="true"><path d="M2 1 L4 1 L4.6 3 L3.4 3.8 Q4.4 5.8 6.2 6.6 L7 5.4 L9 6 L9 8 Q5 9.4 1.4 4.6 Q0.8 3 2 1Z" fill="#d8d9db"/></svg>
        <span>0498716204</span>
      </li>
      <li>
        <svg viewBox="0 0 10 10" aria-hidden="true"><rect x="0.5" y="2" width="9" height="6.5" fill="none" stroke="#d8d9db" stroke-width="1"/><path d="M0.8 2.3 L5 5.6 L9.2 2.3" fill="none" stroke="#d8d9db" stroke-width="1"/></svg>
        <span>info@marlowthread.example.au</span>
      </li>
      <li>
        <svg viewBox="0 0 10 10" aria-hidden="true"><path d="M4 6 L6 4 M3.2 5 L1.8 6.4 a1.5 1.5 0 0 0 2 2 L5.2 7 M6.8 5 L8.2 3.6 a1.5 1.5 0 0 0 -2 -2 L4.8 3" fill="none" stroke="#d8d9db" stroke-width="1"/></svg>
        <span>www.marlowthread.example.au</span>
      </li>
      <li class="gap-before">
        <span class="social-mark" aria-hidden="true"></span>
        <span>_marlow_thread_</span>
      </li>
      <li>
        <span class="social-mark" aria-hidden="true"></span>
        <span>www.fakebookexample.com/marlowthreadau/</span>
      </li>
    </ul>
    <p class="wordmark">Marlow Thread</p>
  </section>

  <section class="card card--front" aria-label="Card front">
    <div class="photo" role="img" aria-label="Misty grey-blue brand photograph filling the card front"></div>
    <p class="wordmark">Marlow Thread</p>
  </section>
</main>
</body>
</html>
```